International business needs business cards

Our company, DRV Ventures Inc. is in the business of supplying a range construction products with particular emphasis on CEMENT. We have developed our own brand - TORVAN SUPPLIES - with which to infiltrate the market. We are launching our brand of cement (TORVAN Type IS Cement) into the Caribbean which is unlike anything this market has ever seen. A monopoly has existed here for the past 60-odd years and the market has now opened to allow the importation of other brands and consumers are anxious and ready for change/improvement. We are very excited to be launching and want to make a great first impression. We will be conducting workshops and seminars (from government level to the hardware store owners) and we want our business card to give us the strong, confident introduction that we need.

Target Market(s)

construction; builders; engineers; home owners

Industry/Entity Type

Construction

Contact Information for Business Card

Marisol Depree
CEO
cell # 1 555 4180736
Ground floor,Lindell Plaza Suite 2734
George Town,Grand Cayman
Cayman Islands,KY1-4823
EMAIL: m.depree@drvventuresinc.example
web site drvventuresinc.example

COMPANY: skype info drv.ventures.example

second card
Yvette Brannock-Depree
CFO
CELL# 1 555 607 3941
George Town,Grand Cayman
Cayman Islands,KY1-4823
EMAIL: y.brannockdepree@drvventuresinc.example
website drvventuresinc.example

Requirements
Must have
• Business cards must display BOTH logos - DRV is the company and TORVAN is the brand.

```html
<!DOCTYPE html>
<html lang="en">
<head>
<meta charset="utf-8">
<title>DRV Ventures Inc. — Business Card</title>
<link rel="stylesheet" href="https://fonts.googleapis.com/css2?family=Source+Sans+3:wght@400;600;700&display=swap">
<style>
  :root {
    --stage-top: #2b2b2b;
    --stage-bottom: #050505;
    --card: #ffffff;
    --brand-red: #821a1a;
    --name-red: #7a1b1b;
    --ink: #1a1a1a;
    --brand-grey: #4a4a4a;
  }
  * { margin: 0; padding: 0; box-sizing: border-box; }
  html, body { width: 1200px; height: 900px; overflow: hidden; }
  body {
    position: relative;
    background: linear-gradient(180deg, var(--stage-top) 0%, #161616 55%, var(--stage-bottom) 100%);
    font-family: "Source Sans 3", "Myriad Pro", Arial, sans-serif;
    color: var(--ink);
  }
  .card {
    position: absolute;
    top: 306px;
    width: 440px;
    height: 271px;
    background: var(--card);
    border-radius: 10px;
  }
  .card--front { left: 149px; }
  .card--back { left: 608px; }

  /* front */
  .front-brand {
    position: absolute;
    left: 40px; top: 67px;
    width: 150px; height: 134px;
    display: flex; align-items: center; gap: 10px;
  }
  .brand-square {
    flex: none;
    width: 40px; height: 40px;
    background: var(--brand-red);
  }
  .brand-name {
    color: var(--brand-red);
    font-weight: 700;
    line-height: 1;
  }
  .brand-name .big { display: block; font-size: 40px; letter-spacing: 1px; }
  .brand-name .small { display: block; font-size: 11px; letter-spacing: 0.5px; margin-top: 3px; }

  .details { position: absolute; left: 210px; top: 54px; }
  .person-name { font-size: 16px; font-weight: 600; color: var(--name-red); line-height: 20px; }
  .person-role { font-size: 12.5px; line-height: 16px; margin-top: 1px; }
  .address { font-size: 12.5px; line-height: 15.5px; margin-top: 15px; }
  .contacts { list-style: none; margin-top: 13px; font-size: 12.5px; line-height: 16px; }
  .contacts li { display: flex; align-items: center; gap: 8px; }
  .contacts svg { width: 8px; height: 8px; flex: none; }

  /* back */
  .back-brand {
    position: absolute;
    left: 139px; top: 69px;
    display: flex; align-items: center; gap: 6px;
  }
  .back-brand .brand-square { width: 67px; height: 66px; }
  .back-brand .brand-name { color: var(--ink); }
  .back-brand .brand-name .big { font-size: 48px; }
  .back-brand .brand-name .small { font-size: 12px; }
  .product-brand {
    position: absolute;
    left: 0; right: 0; top: 190px;
    text-align: center;
    font-size: 13px; font-weight: 700;
    letter-spacing: 1.5px;
    color: var(--brand-grey);
  }
</style>
</head>
<body>
  <section class="card card--front">
    <div class="front-brand">
      <span class="brand-square"></span>
      <span class="brand-name"><span class="big">DRV</span><span class="small">VENTURES INC.</span></span>
    </div>
    <div class="details">
      <p class="person-name">Marisol Depree</p>
      <p class="person-role">CEO</p>
      <p class="address">Ground floor, Lindell Plaza Suite<br>2734 George Town, Grand Cayman<br>Cayman Islands, KY1-4823</p>
      <ul class="contacts">
        <li><svg viewBox="0 0 8 8" aria-hidden="true"><rect x="1.5" y="0" width="5" height="8" rx="1" fill="var(--brand-red)"/><rect x="2.5" y="1" width="3" height="5" fill="#fff"/></svg>1 555 4180736</li>
        <li><svg viewBox="0 0 8 8" aria-hidden="true"><rect x="0" y="1.5" width="8" height="5" fill="var(--brand-red)"/><path d="M0 1.5 L4 4.5 L8 1.5" stroke="#fff" stroke-width="0.8" fill="none"/></svg>m.depree@drvventuresinc.example</li>
        <li><svg viewBox="0 0 8 8" aria-hidden="true"><circle cx="4" cy="4" r="4" fill="var(--brand-red)"/><path d="M2 3 Q4 2 5 4 Q4 6 3 6" stroke="#fff" stroke-width="0.8" fill="none"/></svg>www.drvventuresinc.example</li>
      </ul>
    </div>
  </section>

  <section class="card card--back">
    <div class="back-brand">
      <span class="brand-square"></span>
      <span class="brand-name"><span class="big">DRV</span><span class="small">VENTURES INC.</span></span>
    </div>
    <p class="product-brand">TORVAN SUPPLIES</p>
  </section>
</body>
</html>
```